Cloud-based vaccination website

Basic website design for cloud-based medical company

Coding

Coded - Design and coding required

Number of Pages Required

1 page

Colors
3277b5

```html
<!DOCTYPE html>
<html lang="en">
<head>
<meta charset="utf-8">
<title>Nuvexa – Cloud Vaccine Management</title>
<link href="https://fonts.googleapis.com/css2?family=Rubik:wght@400;500;700&family=Source+Sans+3:wght@400;600&display=swap" rel="stylesheet">
<style>
:root{
  --blue:#3277b5;
  --blue-deep:#1a6fb5;
  --cyan:#1ba9dc;
  --navy:#1d2a6b;
  --card-navy:#0c1f55;
  --ink:#111;
  --body:#3a3a3a;
  --soft:#f4f0f0;
  --footer:#2b2b2b;
  --white:#fff;
}
*{margin:0;padding:0;box-sizing:border-box}
html,body{width:1200px;height:3223px;overflow:hidden}
body{position:relative;background:var(--white);font-family:"Source Sans 3",Arial,sans-serif;color:var(--body)}
.abs{position:absolute}
.head{font-family:"Rubik",Arial,sans-serif}
.btn{position:absolute;display:flex;align-items:center;justify-content:center;background:var(--cyan);color:#fff;font-family:"Rubik",Arial,sans-serif;font-weight:500;border-radius:6px;letter-spacing:.3px}

/* header */
.brand{left:131px;top:30px;display:flex;align-items:center;gap:10px}
.brand-dot{width:30px;height:30px;border-radius:50%;background:var(--cyan)}
.brand-name{font-family:"Rubik",sans-serif;font-weight:500;font-size:40px;color:var(--navy);line-height:1}
.brand-tag{position:absolute;left:131px;top:88px;font-family:"Rubik",sans-serif;font-size:10px;color:var(--navy)}
.follow{left:611px;top:37px;font-size:12px;font-family:"Rubik",sans-serif;color:#222}
.social{top:32px;width:24px;height:24px;border-radius:50%;background:#2a4aa0}
.call-label{left:812px;top:26px;font:500 10px "Rubik",sans-serif;color:#111}
.call-num{left:812px;top:40px;font:500 16px "Rubik",sans-serif;color:#111}
.nav{top:84px;font:500 14px "Rubik",sans-serif;color:#111}
.nav.active{color:var(--cyan);text-decoration:underline}

/* hero */
.hero{left:0;top:120px;width:1200px;height:548px;background:linear-gradient(100deg,#d88a5a 0%,#b24d6a 25%,#6a4a86 55%,#2a2f6e 80%,#141a44 100%)}
.hero-title{left:628px;top:222px;font:700 35px/42px "Rubik",sans-serif;color:#fff}
.dot{top:627px;width:8px;height:8px;border-radius:50%;background:#fff}

/* solutions */
.solutions{left:0;top:668px;width:1200px;height:459px;background:var(--soft)}
.sec-title{width:1200px;left:0;text-align:center;font:700 24px "Rubik",sans-serif;color:var(--ink)}
.sec-sub{width:1200px;left:0;text-align:center;font-size:16px;color:#333}
.rule{height:3px;width:46px;left:577px;background:#aaa}
.sol-card{top:821px;width:222px;height:249px;background:#fff;text-align:center}
.sol-card svg{position:absolute;left:81px;top:34px}
.sol-card h3{position:absolute;top:122px;width:100%;font:500 15px "Rubik",sans-serif;color:#111}
.sol-card p{position:absolute;top:154px;left:22px;width:178px;font-size:13px;line-height:17.5px;color:#333}

/* why */
.why-circle{left:463px;top:1271px;width:274px;height:274px;border-radius:50%;background:#e8f8fc}
.why-icon{width:82px;height:82px;border-radius:50%;background:var(--cyan)}
.why-icon svg{position:absolute;left:21px;top:21px}
.why-item h4{font:500 15px "Rubik",sans-serif;color:#111;margin-bottom:6px}
.why-item p{font-size:13px;line-height:17.5px;color:#333;width:200px}
.why-rule{height:1px;background:#cfcfcf}

/* offer */
.offer-photo{left:0;top:1627px;width:620px;height:446px;background:linear-gradient(90deg,#c9a26a 0%,#d8c7b0 35%,#e9e4de 60%,#1a6fb5 100%)}
.offer-band{left:600px;top:1627px;width:600px;height:446px;background:var(--blue-deep)}
.offer-title{left:634px;top:1678px;font:700 23px "Rubik",sans-serif;color:#fff}
.offer-rule{left:634px;top:1713px;width:48px;height:3px;background:#fff}
.offer-text{left:634px;top:1755px;width:420px;font-size:17px;line-height:24px;color:#fff}

/* resources */
.resources{left:0;top:2073px;width:1200px;height:553px;background:var(--soft)}
.res-card{top:2195px;width:300px;height:369px;background:var(--card-navy)}
.res-img{position:absolute;left:0;top:0;width:300px;height:180px}
.res-card h5{position:absolute;left:27px;top:208px;width:250px;font:500 15px/21px "Rubik",sans-serif;color:#fff}
.res-card p{position:absolute;left:27px;top:258px;width:250px;font-size:11.5px;line-height:16px;color:#dfe6f5}
.res-card .btn{left:27px;top:322px;width:77px;height:22px;font-size:9px;border-radius:4px}

/* cta */
.cta{left:0;top:2626px;width:1200px;height:266px;background:var(--blue-deep)}
.cta-title{left:0;top:2698px;width:1200px;text-align:center;font:700 24px "Rubik",sans-serif;color:#fff}
.cta-sub{left:0;top:2736px;width:1200px;text-align:center;font-size:19px;color:#fff}

/* footer */
.footer{left:0;top:2892px;width:1200px;height:331px;background:var(--footer)}
.f-brand{left:135px;top:2990px;font:500 56px "Rubik",sans-serif;color:#fff;line-height:1}
.f-tag{left:135px;top:3056px;font:400 13px "Rubik",sans-serif;color:#fff}
.f-head{top:2932px;font:700 13px "Rubik",sans-serif;color:#fff;letter-spacing:.5px}
.f-link{left:435px;font-size:12px;color:#fff}
.f-icon{width:24px;height:24px;border-radius:50%;background:#fff}
.f-icon svg{position:absolute;left:6px;top:6px}
.f-text{font-size:12px;line-height:16px;color:#fff}
.f-rule{left:121px;top:3150px;width:934px;height:1px;background:#555}
.copy{left:0;top:3180px;width:1200px;text-align:center;font-size:10px;color:#ddd}
</style>
</head>
<body>

<!-- Header -->
<div class="abs brand"><span class="brand-dot"></span><span class="brand-name">NUVEXA</span></div>
<div class="brand-tag">Modern Digital Software Solutions</div>
<div class="abs follow">FOLLOW</div>
<span class="abs social" style="left:670px"></span>
<span class="abs social" style="left:701px"></span>
<span class="abs social" style="left:732px"></span>
<svg class="abs" style="left:779px;top:32px" width="24" height="24" viewBox="0 0 24 24"><circle cx="12" cy="12" r="10.5" fill="none" stroke="#111" stroke-width="1.6"/><path d="M8.5 7.5l1.8-.5 1 2.3-1.1.9a6 6 0 0 0 3 3l.9-1.1 2.3 1-.5 1.8c-3.8.4-7.8-3.6-7.4-7.4z" fill="#111"/></svg>
<div class="abs call-label">CALL US</div>
<div class="abs call-num">555.010.0199</div>
<div class="btn" style="left:940px;top:25px;width:131px;height:35px;font-size:12px">REQUEST DEMO</div>
<div class="abs nav active" style="left:458px">HOME</div>
<div class="abs nav" style="left:533px">ABOUT US</div>
<div class="abs nav" style="left:639px">SOLUTIONS</div>
<div class="abs nav" style="left:756px">SERVICES</div>
<div class="abs nav" style="left:865px">RESOURCES</div>
<div class="abs nav" style="left:985px">CONTACT US</div>

<!-- Hero -->
<div class="abs hero" role="img" aria-label="Close-up photo of a syringe drawing vaccine from a vial"></div>
<div class="abs hero-title">AN INTEGRATED WORKFLOW<br>FOR VACCINE MANAGEMENT</div>
<div class="btn" style="left:628px;top:325px;width:130px;height:43px;font-size:15px">READ MORE</div>
<span class="abs dot" style="left:562px"></span>
<span class="abs dot" style="left:580px"></span>
<span class="abs dot" style="left:596px;top:624px;width:13px;height:13px;background:none;border:3px solid var(--cyan)"></span>
<span class="abs dot" style="left:616px"></span>
<span class="abs dot" style="left:631px"></span>

<!-- Solutions -->
<div class="abs solutions"></div>
<div class="abs sec-title" style="top:712px">OUR SOLUTIONS</div>
<div class="abs sec-sub" style="top:752px">Lorem Ipsum is simply dummy text of the printing and typesetting</div>

<div class="abs sol-card" style="left:131px">
  <svg width="60" height="64" viewBox="0 0 60 64"><circle cx="34" cy="14" r="12" fill="var(--blue-deep)"/><text x="34" y="20" text-anchor="middle" font-family="Rubik" font-size="16" fill="#fff">$</text><path d="M6 50l10-10c4-3 8-3 12 0h10a3 3 0 0 1 0 6H27h13l12-8a3 3 0 0 1 4 4L40 54H20l-6 6z" fill="var(--blue-deep)"/></svg>
  <h3>Payer Solutions</h3>
  <p>There are many variations of passages of Lorem Ipsum available but the.</p>
</div>
<div class="abs sol-card" style="left:370px">
  <svg width="64" height="64" viewBox="0 0 64 64"><rect x="2" y="6" width="60" height="42" rx="3" fill="var(--blue-deep)"/><rect x="7" y="11" width="50" height="32" fill="#fff"/><circle cx="20" cy="27" r="8" fill="var(--blue-deep)"/><rect x="33" y="24" width="5" height="14" fill="var(--blue-deep)"/><rect x="41" y="18" width="5" height="20" fill="var(--blue-deep)"/><rect x="49" y="28" width="5" height="10" fill="var(--blue-deep)"/><rect x="28" y="48" width="8" height="8" fill="var(--blue-deep)"/><rect x="18" y="56" width="28" height="4" fill="var(--blue-deep)"/></svg>
  <h3>Analytics</h3>
  <p>There are many variations of passages of Lorem Ipsum available but the.</p>
</div>
<div class="abs sol-card" style="left:609px">
  <svg width="64" height="64" viewBox="0 0 64 64"><circle cx="32" cy="30" r="18" fill="var(--blue-deep)"/><circle cx="32" cy="30" r="7" fill="#fff"/><g stroke="var(--blue-deep)" stroke-width="2"><line x1="32" y1="48" x2="32" y2="60"/><line x1="18" y1="44" x2="10" y2="56"/><line x1="46" y1="44" x2="54" y2="56"/></g><circle cx="32" cy="60" r="3" fill="var(--blue-deep)"/><circle cx="10" cy="56" r="3" fill="var(--blue-deep)"/><circle cx="54" cy="56" r="3" fill="var(--blue-deep)"/></svg>
  <h3>Technology</h3>
  <p>There are many variations of passages of Lorem Ipsum available but the.</p>
</div>
<div class="abs sol-card" style="left:850px">
  <svg width="64" height="64" viewBox="0 0 64 64"><circle cx="12" cy="12" r="6" fill="var(--blue-deep)"/><rect x="6" y="20" width="12" height="22" fill="var(--blue-deep)"/><rect x="7" y="42" width="4" height="18" fill="var(--blue-deep)"/><rect x="13" y="42" width="4" height="18" fill="var(--blue-deep)"/><rect x="26" y="6" width="34" height="34" fill="none" stroke="var(--blue-deep)" stroke-width="3"/><rect x="32" y="12" width="8" height="6" fill="var(--blue-deep)"/><rect x="46" y="26" width="8" height="6" fill="var(--blue-deep)"/><path d="M40 15h10v11" fill="none" stroke="var(--blue-deep)" stroke-width="2"/><path d="M36 40l-6 20M50 40l6 20" stroke="var(--blue-deep)" stroke-width="3"/></svg>
  <h3>Optimize Your Workflow</h3>
  <p>There are many variations of passages of Lorem Ipsum available but the.</p>
</div>

<!-- Why choose us -->
<div class="abs sec-title" style="top:1170px">WHY CHOOSE US</div>
<div class="abs rule" style="top:1214px"></div>
<div class="abs why-circle"></div>

<div class="abs why-icon" style="left:131px;top:1274px"><svg width="40" height="40" viewBox="0 0 40 40"><rect x="4" y="26" width="5" height="10" fill="#fff"/><rect x="12" y="22" width="5" height="14" fill="#fff"/><rect x="20" y="18" width="5" height="18" fill="#fff"/><rect x="28" y="12" width="5" height="24" fill="#fff"/><path d="M4 18L16 8l7 5 11-10" fill="none" stroke="#fff" stroke-width="2.5"/></svg></div>
<div class="abs why-item" style="left:236px;top:1273px"><h4>Improve your operations</h4><p>It is a long established fact that a reader will be distracted by the readable content of a page when looking at its layout. The point of using Lorem Ipsum</p></div>
<div class="abs why-rule" style="left:131px;top:1411px;width:294px"></div>
<div class="abs why-icon" style="left:131px;top:1437px"><svg width="40" height="40" viewBox="0 0 40 40"><text x="20" y="33" text-anchor="middle" font-family="Rubik" font-weight="700" font-size="38" fill="#fff">$</text></svg></div>
<div class="abs why-item" style="left:236px;top:1435px"><h4>Reduce cost</h4><p>It is a long established fact that a reader will be distracted by the readable content of a page when looking at its layout. The point of using Lorem Ipsum</p></div>

<div class="abs why-item" style="left:773px;top:1273px"><h4>Manage compliance</h4><p>It is a long established fact that a reader will be distracted by the readable content of a page when looking at its layout. The point of using Lorem Ipsum</p></div>
<div class="abs why-icon" style="left:989px;top:1274px"><svg width="40" height="40" viewBox="0 0 40 40"><rect x="7" y="4" width="26" height="32" rx="3" fill="none" stroke="#fff" stroke-width="2.5"/><rect x="14" y="2" width="12" height="6" rx="2" fill="#fff"/><circle cx="20" cy="24" r="7" fill="none" stroke="#fff" stroke-width="2"/><path d="M16.5 24l2.5 2.5 4.5-5" fill="none" stroke="#fff" stroke-width="2"/></svg></div>
<div class="abs why-rule" style="left:773px;top:1411px;width:297px"></div>
<div class="abs why-item" style="left:773px;top:1435px"><h4>Ensure best practices</h4><p>It is a long established fact that a reader will be distracted by the readable content of a page when looking at its layout. The point of using Lorem Ipsum</p></div>
<div class="abs why-icon" style="left:989px;top:1437px"><svg width="40" height="40" viewBox="0 0 40 40"><rect x="7" y="4" width="26" height="32" rx="3" fill="none" stroke="#fff" stroke-width="2.5"/><g stroke="#fff" stroke-width="2"><path d="M11 12l2 2 3-3M11 20l2 2 3-3M11 28l2 2 3-3"/><line x1="19" y1="13" x2="29" y2="13"/><line x1="19" y1="21" x2="29" y2="21"/><line x1="19" y1="29" x2="29" y2="29"/></g></svg></div>

<!-- What we offer -->
<div class="abs offer-band"></div>
<div class="abs offer-photo" role="img" aria-label="Photo of a smiling woman working on a laptop at a desk"></div>
<div class="abs offer-title">WHAT WE OFFER</div>
<div class="abs offer-rule"></div>
<div class="abs offer-text">There are many variations of passages of Lorem Ipsum available, but the majority have suffered alteration in some form, by injected humour, or randomised words which don't look even slightly believable. If you are going to use a passage of Lorem Ipsum, you need to be sure there isn't anything embarrassing hidden in the middle of text. All the Lorem Ipsum generators on the Internet tend to repeat predefined chunks</div>
<div class="btn" style="left:634px;top:1977px;width:110px;height:36px;font-size:13px">READ MORE</div>

<!-- Resources -->
<div class="abs resources"></div>
<div class="abs sec-title" style="top:2117px">RESOURCES</div>
<div class="abs rule" style="top:2160px"></div>

<div class="abs res-card" style="left:131px">
  <div class="res-img" role="img" aria-label="Photo of hands typing on a laptop keyboard" style="background:linear-gradient(160deg,#f2f2f2,#b9b9bb 60%,#8e8e92)"></div>
  <h5>Lorem Ipsum is simply dummy text of the printing</h5>
  <p>It is a long established fact that a reader will be distracted by the readable content of a page when looking at its layout.</p>
  <div class="btn">READ MORE</div>
</div>
<div class="abs res-card" style="left:455px">
  <div class="res-img" role="img" aria-label="Photo of a syringe and vaccine vial" style="background:linear-gradient(160deg,#cfe3ef,#8fb3cc 55%,#2d4f78)"></div>
  <h5>Lorem Ipsum is simply dummy text of the printing</h5>
  <p>It is a long established fact that a reader will be distracted by the readable content of a page when looking at its layout.</p>
  <div class="btn">READ MORE</div>
</div>
<div class="abs res-card" style="left:772px">
  <div class="res-img" role="img" aria-label="Photo of a smiling woman using a laptop" style="background:linear-gradient(160deg,#e8dfd4,#c9b29a 55%,#6d5a48)"></div>
  <h5>Lorem Ipsum is simply dummy text of the printing</h5>
  <p>It is a long established fact that a reader will be distracted by the readable content of a page when looking at its layout.</p>
  <div class="btn">READ MORE</div>
</div>

<!-- CTA -->
<div class="abs cta"></div>
<div class="abs cta-title">LOREM IPSUM IS SIMPLY DUMMY TEXT OF THE PRINTING</div>
<div class="abs cta-sub">It is a long established fact that a reader will be distracted by the readable</div>
<div class="btn" style="left:535px;top:2785px;width:131px;height:43px;font-size:15px">CONTACT US</div>

<!-- Footer -->
<div class="abs footer"></div>
<div class="abs f-brand">NUVEXA</div>
<div class="abs f-tag">Modern Digital Software Solutions</div>

<div class="abs f-head" style="left:435px">MENU</div>
<div class="abs f-link" style="top:2970px">HOME</div>
<div class="abs f-link" style="top:2990px">ABOUT US</div>
<div class="abs f-link" style="top:3010px">SOLUTIONS</div>
<div class="abs f-link" style="top:3030px">SERVICES</div>
<div class="abs f-link" style="top:3050px">RESOURCES</div>
<div class="abs f-link" style="top:3070px">CONTACT US</div>

<div class="abs f-head" style="left:664px">CONTACT US</div>
<div class="abs f-icon" style="left:664px;top:2972px"><svg width="12" height="12" viewBox="0 0 12 12"><path d="M6 0a4 4 0 0 0-4 4c0 3 4 8 4 8s4-5 4-8a4 4 0 0 0-4-4z" fill="#2b2b2b"/><circle cx="6" cy="4" r="1.5" fill="#fff"/></svg></div>
<div class="abs f-text" style="left:697px;top:2970px">2140 Harbor Lane<br>Fairview, CA 90210</div>
<div class="abs f-icon" style="left:664px;top:3024px"><svg width="12" height="12" viewBox="0 0 12 12"><path d="M1.5 1.5l2.5-.6 1.2 2.8-1.3 1a6 6 0 0 0 3.4 3.4l1-1.3 2.8 1.2-.6 2.5C5.8 10.8 1.2 6.2 1.5 1.5z" fill="#2b2b2b"/></svg></div>
<div class="abs f-text" style="left:697px;top:3022px">Call Us<br>555.0100.0199</div>
<div class="abs f-icon" style="left:664px;top:3075px"><svg width="12" height="12" viewBox="0 0 12 12"><rect x="0" y="2" width="12" height="8" rx="1" fill="#2b2b2b"/><path d="M0.5 2.5L6 7l5.5-4.5" fill="none" stroke="#fff" stroke-width="1"/></svg></div>
<div class="abs f-text" style="left:697px;top:3073px">E mail Us<br>info@nuvexa.com</div>

<div class="abs f-head" style="left:950px">FOLLOW US</div>
<div class="abs f-icon" style="left:949px;top:2972px"></div>
<div class="abs f-text" style="left:983px;top:2970px">Like us on<br>FRIENDLINE</div>
<div class="abs f-icon" style="left:949px;top:3024px"></div>
<div class="abs f-text" style="left:983px;top:3022px">Follow us on<br>CHIRPNET</div>
<div class="abs f-icon" style="left:949px;top:3075px"></div>
<div class="abs f-text" style="left:983px;top:3073px">Follow us on<br>WORKLINK</div>

<div class="abs f-rule"></div>
<div class="abs copy">Copyright © 2021 All Rights Reserved</div>

</body>
</html>
```